Business Card & Email Signature Design || Upmarket + Luxury

Rima Vale Honey, a New Zealand Manuka Honey company needs a Business Card & Email Signature design.

Our logo's are attached in Gold & Black versions, feel free to be creative with how you use the logo and it's patterns in your design.

Style:
- Looking for an Elegant, Luxurious, Upmarket feel.
- Black/Matte Black Card, Gold Foil, UV Embossing

Information to Add:

- Logo
- Company Name: Rima Vale Honey
- Name: Martin Holloway
- Title: Creative Director
- Phone: +64 2815 96 417
- Email: martin@rimavalehoney.example.nz
- Website: www.rimavalehoney.example.nz

- Socials: ***For email Signature Only***
- Facebook: https://www.facebook.com/rimavalehoney/
- Instagram: https://www.instagram.com/rimavalehoney/

Target Market(s)

Asia/Europe Luxury, Upmarket

Contact Information for Business Card

- Logo
- Name: Martin Holloway
- Phone: +64 2815 96 417

Font styles to use
Other font styles liked:
• Champagne & Limousines (Attached)

Requirements
Must have
• Business Card & Email Signature Design.

Looking for a Sleek, Luxury, Upmarket Design.

```html
<!DOCTYPE html>
<html lang="en">
<head>
<meta charset="utf-8">
<title>Rima Vale Honey – Business Card</title>
<link rel="stylesheet" href="https://fonts.googleapis.com/css2?family=Didact+Gothic&display=swap">
<style>
  :root {
    --backdrop: #1c1c1c;
    --card-black: #101317;
    --card-cream: #d8d4c6;
    --cream-light: #e4e1d5;
    --gold: #c8a457;
    --gold-soft: rgba(200, 164, 87, 0.35);
    --ink: #1a1a1a;
    --ink-soft: #3a3a3a;
    --white: #f2f0ea;
  }
  * { box-sizing: border-box; margin: 0; padding: 0; }
  html, body {
    width: 1200px; height: 675px; overflow: hidden;
    background: var(--backdrop);
    font-family: "Didact Gothic", "Century Gothic", sans-serif;
  }
  .canvas {
    position: relative; width: 1200px; height: 675px;
    display: flex; align-items: center; justify-content: center; gap: 80px;
  }
  .card {
    position: relative; width: 420px; height: 240px; overflow: hidden;
    box-shadow: 0 10px 30px rgba(0,0,0,0.45);
  }

  /* Front */
  .card--front { background: var(--card-black); }
  .card--front .comb-pattern {
    position: absolute; left: 0; top: 0; width: 300px; height: 150px;
    background: radial-gradient(ellipse at 20% 20%, rgba(200,164,87,0.22), rgba(60,60,60,0.15) 55%, transparent 80%);
  }
  .front-brand {
    position: absolute; left: 0; right: 0; top: 70px;
    text-align: center; color: var(--gold);
  }
  .brand-dot {
    display: block; width: 44px; height: 44px; margin: 0 auto 16px;
    border: 1.5px solid var(--gold); border-radius: 50%;
  }
  .brand-name {
    font-size: 27px; letter-spacing: 5px; line-height: 1;
  }
  .brand-co {
    font-size: 12px; letter-spacing: 2px; margin-top: 6px;
  }
  .website {
    position: absolute; left: 0; right: 0; bottom: 26px;
    text-align: center; color: var(--white); font-size: 12.5px; letter-spacing: 0.3px;
  }

  /* Back */
  .card--back { background: linear-gradient(135deg, var(--cream-light), var(--card-cream)); }
  .card--back .comb-pattern {
    position: absolute; right: 0; top: 0; width: 220px; height: 140px;
    background: radial-gradient(ellipse at 70% 30%, rgba(255,255,255,0.55), var(--gold-soft) 45%, transparent 78%);
  }
  .seal {
    position: absolute; left: 34px; top: 20px;
    display: flex; align-items: center; gap: 8px;
    color: var(--ink-soft); font-size: 11px; letter-spacing: 1.5px; text-transform: uppercase;
  }
  .seal-circle {
    width: 60px; height: 60px; border: 1.5px solid var(--ink-soft); border-radius: 50%;
  }
  .contact { position: absolute; left: 34px; top: 118px; }
  .job-title {
    display: inline-block; color: var(--ink-soft); font-size: 13px;
    padding-bottom: 2px; border-bottom: 1px solid var(--gold);
  }
  .person-name {
    color: var(--ink); font-size: 30px; line-height: 1.1; margin-top: 4px; letter-spacing: 0.2px;
  }
  .detail {
    display: flex; align-items: center; gap: 10px;
    color: var(--ink); font-size: 12.5px; margin-top: 8px; padding-left: 6px;
  }
  .detail svg { width: 15px; height: 15px; flex: none; }
</style>
</head>
<body>
<main class="canvas">
  <section class="card card--front">
    <div class="comb-pattern" role="img" aria-label="Gold honeycomb line pattern fading across the top left"></div>
    <div class="front-brand">
      <span class="brand-dot"></span>
      <div class="brand-name">RIMA VALE HONEY</div>
      <div class="brand-co">CO.</div>
    </div>
    <div class="website">www.rimavalehoney.example.nz</div>
  </section>

  <section class="card card--back">
    <div class="comb-pattern" role="img" aria-label="Gold honeycomb line pattern in the top right corner"></div>
    <div class="seal">
      <span class="seal-circle"></span>
      <span>Rima Vale Honey</span>
    </div>
    <div class="contact">
      <div class="job-title">Creative Director</div>
      <div class="person-name">MARTIN HOLLOWAY</div>
      <div class="detail">
        <svg viewBox="0 0 24 24" aria-hidden="true"><path fill="#c8a457" d="M6.6 10.8a15.1 15.1 0 0 0 6.6 6.6l2.2-2.2a1 1 0 0 1 1-.25 11.4 11.4 0 0 0 3.6.57 1 1 0 0 1 1 1V20a1 1 0 0 1-1 1A17 17 0 0 1 3 4a1 1 0 0 1 1-1h3.5a1 1 0 0 1 1 1c0 1.25.2 2.45.57 3.57a1 1 0 0 1-.25 1z"/></svg>
        <span>+64 2815 96 417</span>
      </div>
      <div class="detail">
        <svg viewBox="0 0 24 24" aria-hidden="true"><rect x="2.5" y="5.5" width="19" height="13" fill="none" stroke="#c8a457" stroke-width="1.8"/><path d="M2.5 5.5 12 13l9.5-7.5" fill="none" stroke="#c8a457" stroke-width="1.8"/></svg>
        <span>martin@rimavalehoney.example.nz</span>
      </div>
    </div>
  </section>
</main>
</body>
</html>
```